Simple and Clean business card design

We would like the design to be simple clean and to incorporate our colors.

We are open to your design and talent, we have the dots in our logo as we think of it as data points and we connect data points for people.

We are open to see the great creative and clean design you bring to the table

Contact Information for Business Card

please include: name, position, email, phone and website

Font styles to use
Sans Serif

Requirements
Must have
• my colors incorporated, simplicity
Nice to have
• lots of white space, simplicity
Should not have
• complexicity/ complex art

```html
<!DOCTYPE html>
<html lang="en">
<head>
<meta charset="utf-8">
<title>Quillo — Business Card</title>
<link rel="stylesheet" href="https://fonts.googleapis.com/css2?family=Montserrat:wght@400;500;600;700&display=swap">
<style>
  :root {
    --stage: #2b2b2b;
    --card-dark: #000000;
    --card-light: #ffffff;
    --ink: #111111;
    --ink-soft: #9a9a9a;
    --brand-green: #34a853;
    --brand-yellow: #fbbc05;
    --brand-red: #ea4335;
    --brand-blue: #4285f4;
  }
  * { box-sizing: border-box; margin: 0; padding: 0; }
  html, body {
    width: 1200px;
    height: 1015px;
    overflow: hidden;
    background: var(--stage);
    font-family: "Montserrat", sans-serif;
  }
  .canvas {
    position: relative;
    width: 1200px;
    height: 1015px;
  }
  .card {
    position: absolute;
    left: 220px;
    width: 760px;
    height: 434px;
    box-shadow: 0 14px 30px rgba(0,0,0,0.45);
  }
  .card--front { top: 50px; background: var(--card-dark); }
  .card--back  { top: 530px; background: var(--card-light); }

  .wordmark {
    position: absolute;
    display: flex;
    align-items: center;
    gap: 16px;
    font-weight: 600;
    letter-spacing: 1px;
    line-height: 1;
  }
  .wordmark__dot {
    border-radius: 50%;
    background: var(--brand-blue);
    flex: none;
  }
  .card--front .wordmark {
    left: 50%;
    top: 50%;
    transform: translate(-50%, -50%);
    font-size: 110px;
    color: #ffffff;
  }
  .card--front .wordmark__dot { width: 34px; height: 34px; }

  .card--back .wordmark {
    left: 50px;
    top: 50%;
    transform: translateY(-50%);
    font-size: 78px;
    color: var(--ink);
  }
  .card--back .wordmark__dot { width: 26px; height: 26px; }

  .divider {
    position: absolute;
    left: 390px;
    top: 70px;
    width: 1px;
    height: 294px;
    background: var(--ink-soft);
  }

  .contact {
    position: absolute;
    left: 430px;
    top: 96px;
    right: 30px;
    color: var(--ink);
  }
  .contact__name {
    font-size: 30px;
    font-weight: 700;
    line-height: 1.1;
  }
  .contact__role {
    font-size: 20px;
    font-weight: 500;
    color: var(--brand-blue);
    margin-top: 4px;
  }
  .contact__list {
    list-style: none;
    margin-top: 40px;
  }
  .contact__item {
    display: flex;
    align-items: center;
    gap: 12px;
    font-size: 17px;
    font-weight: 500;
    margin-bottom: 12px;
  }
  .contact__icon {
    width: 26px;
    height: 26px;
    flex: none;
  }
  .contact__accent { color: var(--brand-blue); }
</style>
</head>
<body>
<main class="canvas">

  <section class="card card--front" aria-label="Card front">
    <div class="wordmark">
      <span class="wordmark__dot"></span>
      <span class="wordmark__name">quillo</span>
    </div>
  </section>

  <section class="card card--back" aria-label="Card back">
    <div class="wordmark">
      <span class="wordmark__dot"></span>
      <span class="wordmark__name">quillo</span>
    </div>

    <div class="divider"></div>

    <div class="contact">
      <p class="contact__name">Daniel Moreau</p>
      <p class="contact__role">Founder/ CEO</p>
      <ul class="contact__list">
        <li class="contact__item">
          <svg class="contact__icon" viewBox="0 0 26 26" aria-hidden="true">
            <circle cx="13" cy="13" r="13" fill="var(--brand-green)"/>
            <path d="M9 7.5c-1 .6-1.6 1.6-1.3 2.8.8 3.2 4.1 6.5 7.3 7.3 1.2.3 2.2-.3 2.8-1.3l-2.2-1.8-1.4 1c-1.6-.8-2.9-2.1-3.7-3.7l1-1.4z" fill="#fff"/>
          </svg>
          <span>555-014-2290</span>
        </li>
        <li class="contact__item">
          <svg class="contact__icon" viewBox="0 0 26 26" aria-hidden="true">
            <circle cx="13" cy="13" r="13" fill="var(--brand-yellow)"/>
            <rect x="7" y="8.5" width="12" height="9" rx="1" fill="#fff"/>
            <path d="M7.5 9.2 13 13.5l5.5-4.3" fill="none" stroke="var(--brand-yellow)" stroke-width="1.2"/>
          </svg>
          <span>daniel.moreau@quillo.one</span>
        </li>
        <li class="contact__item">
          <svg class="contact__icon" viewBox="0 0 26 26" aria-hidden="true">
            <circle cx="13" cy="13" r="13" fill="var(--brand-red)"/>
            <g fill="none" stroke="#fff" stroke-width="1.2">
              <circle cx="13" cy="13" r="6"/>
              <ellipse cx="13" cy="13" rx="2.6" ry="6"/>
              <path d="M7 13h12M8 10h10M8 16h10"/>
            </g>
          </svg>
          <span>www.<span class="contact__accent">quillo</span>.one</span>
        </li>
      </ul>
    </div>
  </section>

</main>
</body>
</html>
```